KRWB new business card design

We need a business card design for our established business which is Australia wide however based in Melbourne. We are a young team of Financial Planners who specialize in Insurance and Basic super advice for people like us.

We are people who help our clients get things done in a timely and cost effective manner whilst having a good time and a laugh along the way.

We would like this to have a consistent feel with our new e-brochure which i have attached from a color and font perspective.

Industry/Entity Type

Business

Requirements
Must have
• We do not need specific address details rather just the states we are in:

VIC/NSW/QLD/TAS
Nice to have
• Curved edge to mate the brochure

```html
<!DOCTYPE html>
<html lang="en">
<head>
<meta charset="utf-8">
<title>KRWB Business Card Set</title>
<link href="https://fonts.googleapis.com/css2?family=Arimo:ital,wght@0,400;0,700;1,700&family=Jost:ital,wght@0,400;0,500;1,600&family=Source+Sans+3:wght@400&display=swap" rel="stylesheet">
<style>
  :root {
    --stage: #e8e3dc;
    --label: #2a2a2a;
    --green-light: #6cbf4b;
    --green-dark: #00a651;
    --black: #111111;
    --black-soft: #2c2c2c;
    --white: #ffffff;
    --grey-text: #7a7a7a;
    --grey-dark: #404040;
    --shadow: 0 6px 14px rgba(0,0,0,0.35);
  }
  * { margin: 0; padding: 0; box-sizing: border-box; }
  html, body { width: 1200px; height: 788px; overflow: hidden; }
  body { background: var(--stage); position: relative; font-family: "Arimo", Arial, sans-serif; }

  .view-label {
    position: absolute; width: 525px; text-align: center;
    font-family: "Source Sans 3", sans-serif; font-size: 22px; color: var(--label);
  }

  .card {
    position: absolute; width: 525px; height: 300px; border-radius: 22px;
    overflow: hidden; box-shadow: var(--shadow);
  }
  .card--front { left: 53px; top: 72px; background: radial-gradient(circle at 42% 55%, var(--black-soft) 0%, var(--black) 65%); }
  .card--back-one { left: 622px; top: 74px; background: var(--white); }
  .card--back-two { left: 53px; top: 446px; background: var(--white); }
  .card--back-three { left: 622px; top: 446px; background: linear-gradient(180deg, #262626 0%, #0d0d0d 100%); }

  .wave { position: absolute; left: 0; top: 0; width: 525px; height: 160px; }

  .identity { position: absolute; right: 30px; top: 18px; text-align: right; color: var(--white); }
  .identity__name { font-size: 17px; font-weight: 700; line-height: 21px; }
  .identity__line { font-size: 13px; font-weight: 700; line-height: 18px; }

  .contacts { position: absolute; right: 33px; top: 132px; text-align: right; font-family: "Jost", sans-serif; color: var(--white); font-size: 14px; line-height: 26px; }
  .contacts__key { font-weight: 600; font-style: italic; margin-right: 3px; }

  .brand { position: absolute; display: flex; flex-direction: column; align-items: flex-start; gap: 14px; }
  .brand__square { width: 70px; height: 70px; background: var(--green-light); }
  .brand__name { font-family: "Arimo", Arial, sans-serif; font-weight: 700; font-size: 34px; letter-spacing: 1px; line-height: 1; }
  .brand--front { left: 48px; top: 150px; }
  .brand--front .brand__name { color: var(--white); }
  .brand--back-one { left: 78px; top: 80px; }
  .brand--back-one .brand__name { color: var(--black); }
  .brand--back-three { left: 66px; top: 70px; }
  .brand--back-three .brand__square { width: 110px; height: 110px; }
  .brand--back-three .brand__name { color: var(--white); font-size: 40px; }

  .divider { position: absolute; left: 261px; top: 18px; width: 2px; height: 236px; background: linear-gradient(180deg, rgba(0,0,0,0) 0%, #555 50%, rgba(0,0,0,0) 100%); }

  .services { position: absolute; list-style: none; }
  .services__title { font-size: 18px; font-weight: 700; font-style: italic; margin-bottom: 14px; }
  .services__item { font-size: 14px; font-weight: 700; line-height: 34px; }
  .services__item::before { content: "\25AA"; margin-right: 6px; }
  .services--back-one { left: 320px; top: 45px; color: var(--grey-text); }
  .services--back-two { left: 0; width: 525px; top: 46px; text-align: center; color: var(--grey-dark); }
  .services--back-three { left: 313px; top: 24px; color: var(--white); }

  .tagline-band { position: absolute; left: 0; bottom: 0; width: 100%; height: 38px; background: var(--green-light); color: var(--white); font-size: 14px; font-weight: 700; text-align: center; line-height: 38px; }
  .tagline { position: absolute; font-size: 14px; font-weight: 700; }
  .tagline--back-two { left: 0; width: 525px; bottom: 17px; text-align: center; color: var(--grey-dark); }
  .tagline--back-three { left: 313px; top: 252px; color: var(--green-light); line-height: 18px; }
</style>
</head>
<body>
  <div class="view-label" style="left:53px; top:32px;">Front</div>
  <div class="view-label" style="left:622px; top:32px;">Back - 1</div>
  <div class="view-label" style="left:53px; top:402px;">Back - 2</div>
  <div class="view-label" style="left:622px; top:402px;">Back - 3</div>

  <section class="card card--front">
    <svg class="wave" viewBox="0 0 525 160" aria-hidden="true">
      <path d="M0,0 H525 V110 C460,114 380,126 280,138 C180,148 80,138 0,84 Z" fill="#000" opacity="0.6"/>
      <path d="M0,0 H525 V102 C460,106 380,118 280,130 C180,140 80,130 0,76 Z" fill="var(--green-dark)"/>
      <path d="M0,0 H525 V91 C460,95 380,107 280,119 C180,129 80,119 0,65 Z" fill="var(--white)"/>
      <path d="M0,0 H525 V88 C460,92 380,104 280,116 C180,126 80,116 0,62 Z" fill="var(--green-light)"/>
    </svg>
    <div class="identity">
      <p class="identity__name">Liam Hartwell</p>
      <p class="identity__line">ADFS, BBus, LRS©</p>
      <p class="identity__line">Financial Adviser</p>
    </div>
    <div class="contacts">
      <p><span class="contacts__key">c</span> 0400 555 218</p>
      <p><span class="contacts__key">p</span> 1300 555 740</p>
      <p><span class="contacts__key">f</span> 03 9555 0142</p>
      <p><span class="contacts__key">e</span> liam@krwb.com.au</p>
      <p><span class="contacts__key">w</span> www.krwb.com.au</p>
      <p>VIC/NSW/QLD/TAS</p>
    </div>
    <div class="brand brand--front">
      <span class="brand__square"></span>
      <span class="brand__name">KRWB</span>
    </div>
  </section>

  <section class="card card--back-one">
    <div class="brand brand--back-one">
      <span class="brand__square"></span>
      <span class="brand__name">KRWB</span>
    </div>
    <div class="divider"></div>
    <ul class="services services--back-one">
      <li class="services__title">Specialising in</li>
      <li class="services__item">Risk Insurance</li>
      <li class="services__item">Debt Management</li>
      <li class="services__item">Superannuation</li>
      <li class="services__item">Wealth Creation</li>
      <li class="services__item">Retirement Planning</li>
    </ul>
    <div class="tagline-band">SECURE FUTURE, ENHANCED LIFESTYLE</div>
  </section>

  <section class="card card--back-two">
    <ul class="services services--back-two">
      <li class="services__title">Specialising in</li>
      <li class="services__item">Risk Insurance</li>
      <li class="services__item">Debt Management</li>
      <li class="services__item">Superannuation</li>
      <li class="services__item">Wealth Creation</li>
      <li class="services__item">Retirement Planning</li>
    </ul>
    <p class="tagline tagline--back-two">SECURE FUTURE, ENHANCED LIFESTYLE</p>
  </section>

  <section class="card card--back-three">
    <div class="brand brand--back-three">
      <span class="brand__square"></span>
      <span class="brand__name">KRWB</span>
    </div>
    <ul class="services services--back-three">
      <li class="services__title">Specialising in</li>
      <li class="services__item">Risk Insurance</li>
      <li class="services__item">Debt Management</li>
      <li class="services__item">Superannuation</li>
      <li class="services__item">Wealth Creation</li>
      <li class="services__item">Retirement Planning</li>
    </ul>
    <p class="tagline tagline--back-three">SECURE FUTURE<br>ENHANCED LIFESTYLE</p>
  </section>
</body>
</html>
```